Kelvor Engineers: Why you should hire us keepsake

New design. Open to plastic cards. We are an engineering firm that designs cell phone towers and commercial buildings. Please check out our website www.kelvorstruct.com for more details. We want people to remember our card and for it to be useful if possible. We want the same look and feel on these cards to be translated to other marketing material we may need such as brochures.

Target Market(s)

Architects, Developers and Telecommunication Carriers

Industry/Entity Type

Engineering

Contact Information for Business Card

Card with our company colors, logo, and innovative design with elements related to our industry.

Font styles to use
Sans Serif

Colors
9bcb3c
abd036
0255a3

Requirements
Must have
• Sleek and hip design
Nice to have
• Bright lime green and navy coloring that pops with an innovative design.
Should not have
• A basic and boring design

```html
<!DOCTYPE html>
<html lang="en">
<head>
<meta charset="utf-8">
<title>Kelvor Engineers – Business Card</title>
<link rel="stylesheet" href="https://fonts.googleapis.com/css2?family=Roboto:wght@400;900&family=Roboto+Condensed:wght@500;700&display=swap">
<style>
  :root {
    --lime: #1aff00;
    --navy: #0b2d5e;
    --ink: #1a1b1d;
    --paper: #f1f1f1;
    --grey-text: #555555;
    --rule: #b8b8b8;
    --backdrop: #e4e4e4;
  }
  * { margin: 0; padding: 0; box-sizing: border-box; }
  html, body { width: 1200px; height: 960px; overflow: hidden; }
  body {
    position: relative;
    background: var(--backdrop);
    font-family: "Roboto", Arial, sans-serif;
  }
  .card {
    position: absolute;
    left: 320px;
    width: 600px;
    border-radius: 20px;
    overflow: hidden;
  }
  .card-front { top: 108px; height: 345px; background: var(--ink); }
  .card-back  { top: 493px; height: 342px; background: var(--paper); }

  .wordmark {
    position: absolute;
    font-family: "Roboto", Arial, sans-serif;
    font-weight: 900;
    color: var(--lime);
    letter-spacing: -2px;
    line-height: 1;
  }
  .card-front .wordmark {
    left: 0; right: 0; top: 110px;
    text-align: center;
    font-size: 112px;
  }
  .tagline {
    position: absolute;
    left: 0; right: 0; top: 265px;
    display: flex; justify-content: center; align-items: center; gap: 4px;
    font-family: "Roboto Condensed", Arial, sans-serif;
    font-weight: 700;
    font-size: 17.5px;
    color: #eaffe6;
    letter-spacing: 0.1px;
  }
  .tagline::before, .tagline::after {
    content: ""; width: 27px; height: 1.5px; background: #ffffff;
  }
  .cities {
    position: absolute;
    left: 0; right: 0; top: 287px;
    text-align: center;
    font-size: 15.5px;
    color: #ffffff;
    letter-spacing: 0.6px;
  }

  .card-back .wordmark {
    right: 40px; top: 46px;
    font-size: 78px;
  }
  .holder-name {
    position: absolute;
    left: 31px; top: 204px;
    font-family: "Roboto Condensed", Arial, sans-serif;
    font-weight: 700;
    font-size: 22px;
    color: var(--lime);
  }
  .divider {
    position: absolute;
    left: 30px; top: 237px;
    width: 530px; height: 1.5px;
    background: var(--rule);
  }
  .contact-list {
    position: absolute;
    left: 32px; top: 250px;
    list-style: none;
  }
  .contact-list li {
    display: flex; align-items: center; gap: 7px;
    height: 19px;
    font-size: 14.5px;
    color: var(--grey-text);
  }
  .contact-list svg { width: 14px; height: 14px; fill: var(--lime); }
  .website {
    position: absolute;
    right: 40px; top: 287px;
    font-size: 14.5px;
    color: var(--grey-text);
    letter-spacing: 0.5px;
  }
  .brand-band {
    position: absolute;
    left: 0; bottom: 0;
    width: 600px; height: 12px;
  }
</style>
</head>
<body>

<section class="card card-front" aria-label="Card front">
  <div class="wordmark">KELVOR</div>
  <div class="tagline">MULTI-DISCIPLINE ENGINEERING</div>
  <div class="cities">Northgate | Carlow Bay | Westhaven | Port Alden</div>
</section>

<section class="card card-back" aria-label="Card back">
  <div class="wordmark">KELVOR</div>
  <div class="holder-name">DANA HOLLOWAY REYES</div>
  <div class="divider"></div>
  <ul class="contact-list">
    <li>
      <svg viewBox="0 0 16 16" aria-hidden="true"><path d="M3.6 1.2l2.3 2.6-1.3 2.1c.9 2 2.5 3.6 4.5 4.5l2.1-1.3 2.6 2.3-1.2 2.4C7 13.6 2.4 9 1.2 2.4z"/></svg>
      555.014.2290
    </li>
    <li>
      <svg viewBox="0 0 16 16" aria-hidden="true"><path d="M4 1h8v14H4zM5.5 3v9h5V3zM7.2 13h1.6v1H7.2z" fill-rule="evenodd"/></svg>
      555.017.4431
    </li>
    <li>
      <svg viewBox="0 0 16 16" aria-hidden="true"><path d="M1 4h14v9H1zM1 4l7 5 7-5"/></svg>
      dreyes@kelvorstruct.com
    </li>
  </ul>
  <div class="website">www.kelvorstruct.com</div>
  <svg class="brand-band" viewBox="0 0 600 12" preserveAspectRatio="none" aria-hidden="true">
    <polygon points="0,0 394,0 390,12 0,12" fill="var(--lime)"/>
    <polygon points="396,0 600,0 600,12 392,12" fill="var(--navy)"/>
  </svg>
</section>

</body>
</html>
```